Luxury Business Card Design for High-End Window Treatments

Gilded Slatworks
Custom Plantation Shutters & Architectural Shading Systems

⸻

BACK

Daniel Trevick
Owner

Custom Interior & Exterior Window Treatments

919-555-0148
gildedslatworks.com

I have included a picture that I’m hoping we can use on the back, but I’m also wondering if you can get rid of the ladder? Should we get rid of shutters , shades and blinds underneath Gilded Slatworks?

Target Market(s)

High-end residential homeowners, custom home builders, architects, interior designers, and luxury renovation clients seeking premium plantation shutters and motorized architectural shading systems.

Industry/Entity Type

Custom Window treatments

Contact Information for Business Card

Front Gilded Slatworks Custom Plantation Shutters Motorized Architectural Shading Systems BACK Daniel Trevick Owner 919-555-0148 GildedSlatworks.com Custom Interior & Exterior Window Treatments By Appointment

Requirements
Nice to have
• Not 100% sure on nice to halves or the color but you can definitely check out my website to get a better understanding of what I’m trying to do

```html
<!DOCTYPE html>
<html lang="en">
<head>
<meta charset="utf-8">
<title>Gilded Slatworks — Business Card</title>
<link rel="stylesheet" href="https://fonts.googleapis.com/css2?family=Playfair+Display:wght@400;700&family=Montserrat:wght@400;500&family=Roboto:wght@700&display=swap">
<style>
  :root {
    --stage: #cfcfcf;
    --ink: #050505;
    --gold: #c4aa52;
    --gold-deep: #b79c45;
    --white: #f4f4f4;
    --photo-sky: #2b3340;
    --photo-house: #9a9a94;
    --photo-green: #3f5a2e;
  }
  * { margin: 0; padding: 0; box-sizing: border-box; }
  html, body { width: 1200px; height: 800px; overflow: hidden; }
  body {
    position: relative;
    background: radial-gradient(circle at 70% 20%, #dcdcdc, var(--stage) 55%, #a9a9a9);
    font-family: "Montserrat", sans-serif;
  }
  .card {
    position: absolute;
    width: 600px;
    height: 343px;
    overflow: hidden;
    box-shadow: 0 14px 30px rgba(0,0,0,0.28);
  }

  /* Back card */
  .card-back { left: 80px; top: 40px; background: var(--ink); }
  .card-back .photo {
    position: absolute; inset: 0;
    clip-path: polygon(58% 0, 100% 0, 100% 100%, 78% 100%, 44% 0);
    clip-path: polygon(42% 0, 100% 0, 100% 100%, 62% 100%);
    background:
      linear-gradient(180deg, var(--photo-sky) 0%, var(--photo-house) 45%, #6e6a5e 62%, var(--photo-green) 78%, #5b5a4a 100%);
  }
  .card-back .details {
    position: absolute; left: 40px; top: 52px; width: 300px;
  }
  .name {
    font-family: "Playfair Display", serif;
    font-weight: 700; font-size: 30px; color: var(--gold); line-height: 1.1;
  }
  .role { font-size: 17px; color: var(--white); margin-top: 2px; }
  .rule { width: 110px; height: 1px; background: var(--gold); margin: 16px 0; }
  .contact { list-style: none; }
  .contact li {
    display: flex; align-items: center; gap: 10px;
    font-size: 17px; color: var(--white); line-height: 1.45;
  }
  .contact svg { width: 16px; height: 16px; flex: none; }
  .tagline {
    font-family: "Playfair Display", serif;
    font-size: 18px; color: var(--gold); line-height: 1.35;
  }

  /* Front card */
  .card-front { left: 520px; top: 417px; background: var(--gold); }
  .card-front .dark-field {
    position: absolute; inset: 0; background: var(--ink);
    clip-path: polygon(72% 0, 100% 0, 100% 100%, 44% 100%);
    clip-path: polygon(58% 0, 100% 0, 100% 100%, 40% 100%);
  }
  .services {
    position: absolute; left: 34px; top: 118px; list-style: none;
    font-family: "Roboto", sans-serif; font-weight: 700; font-size: 17px; color: var(--ink);
  }
  .services li { display: flex; align-items: center; gap: 10px; margin-bottom: 18px; }
  .services li::before {
    content: ""; width: 7px; height: 7px; background: var(--ink); transform: rotate(45deg); flex: none;
  }
  .wordmark {
    position: absolute; right: 34px; top: 116px; text-align: left;
    font-family: "Playfair Display", serif; font-weight: 400;
    font-size: 46px; line-height: 1.05; color: var(--gold);
  }
  .wordmark span { display: block; }
  .wordmark span + span { padding-left: 40px; }
</style>
</head>
<body>

<section class="card card-back" aria-label="Business card back">
  <div class="photo" role="img" aria-label="Photograph of a home's covered porch with white columns, screened windows, shrubs and Adirondack chairs"></div>
  <div class="details">
    <h1 class="name">Daniel Trevick</h1>
    <p class="role">Owner</p>
    <div class="rule"></div>
    <ul class="contact">
      <li>
        <svg viewBox="0 0 16 16" aria-hidden="true"><path d="M4 1.5l2.2 3-1.3 1.6c.8 1.9 2.2 3.3 4 4l1.6-1.3 3 2.2-1.2 2.5C7 13.3 2.7 9 2 3.7z" fill="var(--gold)"/></svg>
        919-555-0148
      </li>
      <li>
        <svg viewBox="0 0 16 16" aria-hidden="true"><rect x="1" y="3.5" width="14" height="9" fill="var(--gold)"/><path d="M1 3.5l7 5 7-5" fill="none" stroke="var(--ink)" stroke-width="1.2"/></svg>
        GildedSlatworks.com
      </li>
    </ul>
    <div class="rule"></div>
    <p class="tagline">Custom Interior &amp; Exterior<br>Window Treatments<br>By Appointment</p>
  </div>
</section>

<section class="card card-front" aria-label="Business card front">
  <div class="dark-field"></div>
  <ul class="services">
    <li>Gilded Slatworks Custom</li>
    <li>Plantation Shutters Motorized</li>
    <li>Architectural Shading Systems</li>
  </ul>
  <p class="wordmark"><span>Gilded</span><span>Slatworks</span></p>
</section>

</body>
</html>
```